Business card design for a dynamic IT consulting company

We need a business card design for a young firm, specialized in the Telecommunications/Consulting industry. The name of the company is Quindor and Partners Business Consulting Ltd. (Short name: Quindor and Partnes)
Quindor = solve read reverse, so we aim to be uncomplicated and solution-oriented. The small pipe in our logo is also related to the word solve. So we need a new business card design, which is simple, eye catching and something non traditional (I would probably prefer a square shaped design rather than a rectangle, but open for suggestions). Attached our logo.

Target Market(s)

Usually our customers are Tier1 Telecoms providers (Q-Netra, Palorix, etc) and their executives.

Industry/Entity Type

Business

Contact Information for Business Card

Name: Bence Tolnavari
Email: b.tolnavari@quindor.hu
Web: www.quindor.hu
Mobile: +36 30 518 2769
Title: Managing Director

Optional:
Company name: Quindor and Partners Ltd.
Address: 1087 Budapest, Tolvenka str. 28/C, Hungary

Font styles to use
Other font styles liked:
• helveticaneue_medium, Prime Regular are used now.

Colors

Designer to choose colors to be used in the design.

Requirements
Must have
• I would like to have a 2 sided design.
Nice to have
• I thought if we make the logo a bit bigger (without the company name), that could go to the back with the company name below. I though, if the pipe in the logo is somehow touchable on the business card, would be nice and unique.

```html
<!DOCTYPE html>
<html lang="en">
<head>
<meta charset="utf-8">
<title>Quindor and Partners – Business Card</title>
<link href="https://fonts.googleapis.com/css2?family=Arimo:wght@400;700&display=swap" rel="stylesheet">
<style>
  :root {
    --backdrop: #e2e2e2;
    --card-white: #f4f4f4;
    --card-dark: #606163;
    --brand-blue: #1a9ad6;
    --brand-magenta: #b5308f;
    --text-grey: #555759;
    --text-light: #ffffff;
  }
  * { box-sizing: border-box; margin: 0; padding: 0; }
  html, body {
    width: 1200px; height: 960px; overflow: hidden;
    background: var(--backdrop);
    font-family: "Arimo", Arial, sans-serif;
  }
  .stage { position: relative; width: 1200px; height: 960px; }
  .card { position: absolute; top: 305px; width: 343px; height: 343px; overflow: hidden; }

  /* Front */
  .card-front { left: 200px; background: var(--card-white); }
  .side-stripe {
    position: absolute; left: 24px; top: 0; width: 34px; height: 100%;
    background: var(--brand-blue);
  }
  .stripe-gap {
    position: absolute; left: 24px; top: 50px; width: 34px; height: 40px;
    background: var(--card-white);
  }
  .brand {
    position: absolute; left: 68px; top: 53px; height: 34px;
    display: flex; align-items: center;
    border-left: 1px solid var(--text-grey); padding-left: 8px;
    font-size: 24px; color: var(--text-grey); letter-spacing: -0.2px;
  }
  .icon { position: absolute; left: 33px; width: 16px; height: 16px; fill: var(--text-light); }
  .icon-person { top: 145px; }
  .icon-pin { top: 202px; }
  .icon-phone { top: 255px; }
  .icon-mail { top: 277px; height: 12px; }

  .person-name {
    position: absolute; left: 76px; top: 133px;
    font-size: 20px; font-weight: 700; color: var(--brand-blue);
  }
  .person-title {
    position: absolute; left: 76px; top: 157px;
    font-size: 16px; color: var(--text-grey);
  }
  .contact-block {
    position: absolute; left: 76px;
    font-size: 14px; line-height: 18px; color: var(--text-grey);
  }
  .address { top: 187px; }
  .reach { top: 254px; }

  /* Back */
  .card-back { left: 651px; background: var(--card-dark); }
  .back-brand {
    position: absolute; left: 0; right: 0; top: 150px;
    display: flex; justify-content: center; align-items: center; gap: 12px;
    font-size: 30px; color: var(--text-light);
  }
  .back-brand .brand-square { width: 16px; height: 16px; background: var(--brand-magenta); }
  .web-address {
    position: absolute; left: 0; right: 0; top: 292px; text-align: center;
    font-size: 13px; letter-spacing: 0.6em; color: var(--text-light);
  }
</style>
</head>
<body>
<main class="stage">

  <section class="card card-front" aria-label="Business card front">
    <div class="side-stripe"></div>
    <div class="stripe-gap"></div>
    <div class="brand">Quindor &amp; Partners</div>

    <svg class="icon icon-person" viewBox="0 0 16 16" aria-hidden="true">
      <circle cx="8" cy="5" r="3.6"/>
      <path d="M1 16c0-4 3-6.5 7-6.5s7 2.5 7 6.5z"/>
    </svg>
    <svg class="icon icon-pin" viewBox="0 0 16 16" aria-hidden="true">
      <path d="M8 0a5.5 5.5 0 0 0-5.5 5.5C2.5 10 8 16 8 16s5.5-6 5.5-10.5A5.5 5.5 0 0 0 8 0zm0 7.8a2.3 2.3 0 1 1 0-4.6 2.3 2.3 0 0 1 0 4.6z"/>
    </svg>
    <svg class="icon icon-phone" viewBox="0 0 16 16" aria-hidden="true">
      <path d="M4.5 0h7a1 1 0 0 1 1 1v14a1 1 0 0 1-1 1h-7a1 1 0 0 1-1-1V1a1 1 0 0 1 1-1zm.8 2v10h5.4V2z"/>
    </svg>
    <svg class="icon icon-mail" viewBox="0 0 16 12" aria-hidden="true">
      <path d="M1 1h14v10H1z M1.5 1.5L8 7l6.5-5.5" stroke="#1a9ad6" stroke-width="1.2"/>
    </svg>

    <h1 class="person-name">BENCE TOLNAVARI</h1>
    <p class="person-title">MANAGING DIRECTOR</p>
    <p class="contact-block address">Quindor and Partners Ltd.<br>1087 Budapest<br>Tolvenka str. 28/C, Hungary</p>
    <p class="contact-block reach">+36 30 518 2769<br>b.tolnavari@quindor.hu</p>
  </section>

  <section class="card card-back" aria-label="Business card back">
    <div class="back-brand"><span class="brand-square"></span>Quindor</div>
    <p class="web-address">www.quindor.hu</p>
  </section>

</main>
</body>
</html>
```